Business Card Design For Office Furniture Clearance Company

Kestrel Office Clearance - our company name pretty much explains what we do, we clear offices for high end clients, mainly plc's and large international companies.

We require a nice looking business card that displays professionalism but without being too serious.

It would be nice to see just a little more than a conventional boring business card, make sure you add some flare.

Industry/Entity Type

Office Furniture

Contact Information for Business Card

CARD 1

Mark Holloway
Director
mark@kestrelofficeclearance.co.uk
m: 07700 153928

t: 01632 960418
www.kestrelofficeclearance.co.uk

Kestrel Office Clearance
Unit K4 B
2-8 Fenwick Lane
Harwick
Eastmoor Vale
ZZ9 4QT

free office clearances… you cant get better than that.

CARD 2

Peter Radford
Director
peter@kestrelofficeclearance.co.uk
m: 07700 382615

t: 01632 960418

Kestrel Office Clearance
Unit K4 B
2-8 Fenwick Lane
Harwick
Eastmoor Vale
ZZ9 4QT

Font styles to use
Sans Serif

Requirements
Must have
• A white background - as we have a blue logo.
Nice to have
• Nice use of the logo - play around with this and dissect it.

```html
<!DOCTYPE html>
<html lang="en">
<head>
<meta charset="utf-8">
<title>Kestrel Office Clearance – Business Card</title>
<link rel="stylesheet" href="https://fonts.googleapis.com/css2?family=Montserrat:wght@400;500;600;700&display=swap">
<style>
  :root {
    --brand-blue: #1a7cbd;
    --ink: #1c1c1c;
    --text-grey: #3a3a3a;
    --paper: #ffffff;
    --backdrop: #e9ebee;
  }
  * { box-sizing: border-box; margin: 0; padding: 0; }
  html, body { width: 1200px; height: 900px; overflow: hidden; }
  body {
    background: var(--backdrop);
    font-family: "Montserrat", sans-serif;
    position: relative;
  }
  .card {
    position: absolute;
    left: 270px;
    width: 660px;
    height: 380px;
    background: var(--paper);
    border-radius: 24px;
    box-shadow: 0 6px 20px rgba(0,0,0,0.12);
  }
  .card--front { top: 50px; }
  .card--back { top: 470px; }

  .brand-disc {
    position: absolute;
    border-radius: 50%;
    background: var(--brand-blue);
    display: flex;
    align-items: center;
    justify-content: center;
  }
  .card--front .brand-disc { width: 250px; height: 250px; left: 205px; top: 36px; }
  .brand-disc__name {
    color: var(--paper);
    font-weight: 700;
    font-size: 30px;
    letter-spacing: 1px;
    text-transform: uppercase;
  }
  .tagline {
    position: absolute;
    left: 40px;
    right: 40px;
    bottom: 36px;
    font-weight: 600;
    font-size: 15px;
    letter-spacing: 1px;
    color: var(--ink);
    text-transform: uppercase;
    white-space: nowrap;
  }

  .card--back .brand-disc { width: 240px; height: 240px; left: 40px; top: 36px; }
  .company-name {
    position: absolute;
    left: 20px;
    width: 280px;
    top: 300px;
    text-align: center;
    font-weight: 700;
    font-size: 17px;
    color: var(--ink);
    text-transform: uppercase;
    white-space: nowrap;
  }
  .divider {
    position: absolute;
    left: 318px;
    top: 44px;
    width: 2px;
    height: 286px;
    background: var(--brand-blue);
  }
  .contact {
    position: absolute;
    left: 336px;
    top: 40px;
    right: 16px;
    color: var(--text-grey);
  }
  .contact__name {
    color: var(--brand-blue);
    font-weight: 700;
    font-size: 26px;
    text-transform: uppercase;
    line-height: 1.1;
  }
  .contact__role {
    font-size: 14px;
    font-weight: 500;
    text-transform: uppercase;
    margin-bottom: 6px;
  }
  .contact__list { list-style: none; font-size: 14.5px; line-height: 1.5; }
  .contact__list li { display: flex; align-items: center; gap: 8px; white-space: nowrap; }
  .contact__list svg { width: 13px; height: 13px; flex: none; fill: none; stroke: var(--brand-blue); stroke-width: 2; }
  .address { font-style: normal; font-size: 16px; line-height: 1.35; margin-top: 6px; margin-left: 21px; }
</style>
</head>
<body>

<section class="card card--front">
  <div class="brand-disc"><span class="brand-disc__name">Kestrel</span></div>
  <p class="tagline">Zero-cost office clearances... simply the smart choice</p>
</section>

<section class="card card--back">
  <div class="brand-disc"></div>
  <p class="company-name">Kestrel Office Clearance</p>
  <div class="divider"></div>
  <div class="contact">
    <h1 class="contact__name">Mark Holloway</h1>
    <p class="contact__role">Director</p>
    <ul class="contact__list">
      <li><svg viewBox="0 0 24 24"><rect x="6" y="2" width="12" height="20" rx="2"/><line x1="11" y1="18" x2="13" y2="18"/></svg>07700 153928</li>
      <li><svg viewBox="0 0 24 24"><path d="M5 3h4l2 5-3 2a11 11 0 0 0 6 6l2-3 5 2v4a2 2 0 0 1-2 2A18 18 0 0 1 3 5a2 2 0 0 1 2-2z"/></svg>01632 960418</li>
      <li><svg viewBox="0 0 24 24"><rect x="2" y="5" width="20" height="14" rx="1"/><polyline points="2,5 12,13 22,5"/></svg>mark@kestrelofficeclearance.co.uk</li>
      <li><svg viewBox="0 0 24 24"><circle cx="12" cy="12" r="10"/><ellipse cx="12" cy="12" rx="4" ry="10"/><line x1="2" y1="12" x2="22" y2="12"/></svg>www.kestrelofficeclearance.co.uk</li>
    </ul>
    <address class="address">
      Kestrel Office Clearance<br>
      Unit K4 B<br>
      2-8 Fenwick Lane<br>
      Harwick<br>
      Eastmoor Vale<br>
      ZZ9 4QT
    </address>
  </div>
</section>

</body>
</html>
```